The Brightwater Hour (By Line: Making an Impact through Effective Leadership)

I am seeking the design and creation of a”banner ad image” for my radio program entitled “The Brightwater Hour.” The banner created should capture the look and feel of an image that reflects the vision statement below and that fosters the intent reflected by the principal goals listed below:

Vision statement

The Brightwater Hour is a powerfully engaging platform for great conversations about leadership and leadership learning.

Goals

1. Build a community of listeners who will be made to feel invited and excited about being connected to the show, it host and its broader community of listeners.

2. Provide interesting, intelligent and meaningful conversations about leadership and learning by the host, invited guests, both in studio and online.
The banner should be one that speaks to/invites listeners to become members of a community of listeners seeking to listen to and learn about the subject of leadership and leadership improvement.

The acceptable (final) banner should be professional in image, style and substance. The Photo shop layered file is required so that the banner image can be altered and adapted for use in PDF or text documents.

Finally, it is a banner that I intend to repopulate across several medium’s, such as pelzor, grip tally, etc. as a part of the process of establishing an image – brand – for the radio show as reflected the vision statement and goals.

While the target audience described is broad, it is anticipated that the primary listeners will be those who are leaders and serving in such roles as CEO’s, Vice Presidents, and other leaders in business, government and other local organizational capacities including students interested in learning about and discussing the subject of leadership.

Target Market(s)

Those who are interested in the topic of leadership and are actively engaged in leading as supervisors, managers and executives. These would be CEO, VP, and other C-level leaders in business, private and public sector organizations. It is also anticipated that those who are students of leadership learning will find my program a great resource.

Industry/Entity Type

Radio

Colors
3176b5
b768aa
d3a5cc

Requirements
Must have
• Be unique, attractive and capture the look and feel as noted in the description of the project.
Nice to have
• Note: I will have a head shot photo included in the banner so a place holder needs to be included for that

```html
<!DOCTYPE html>
<html lang="en">
<head>
<meta charset="utf-8">
<title>Brightwater Hour – Banner Set</title>
<link rel="stylesheet" href="https://fonts.googleapis.com/css2?family=Ubuntu:wght@700&family=Open+Sans:wght@300&display=swap">
<style>
  :root {
    --page-bg: #cfcfcf;
    --banner-bg: #000000;
    --photo-dark: #0d0e10;
    --photo-mid: #2b2d31;
    --photo-light: #8d8d8b;
    --title-white: #ffffff;
    --cta-bg: #2a2a2a;
    --cta-red: #e0202a;
  }
  * { margin: 0; padding: 0; box-sizing: border-box; }
  html, body { width: 1200px; height: 1200px; overflow: hidden; }
  body { background: var(--page-bg); position: relative; }

  .banner { position: absolute; background: var(--banner-bg); overflow: hidden; }
  .photo {
    position: absolute;
    background: radial-gradient(ellipse at 50% 55%, var(--photo-light) 0%, var(--photo-mid) 35%, var(--photo-dark) 75%);
  }
  .title {
    position: absolute;
    font-family: "Ubuntu", sans-serif;
    font-weight: 700;
    color: var(--title-white);
    line-height: 1.2;
    white-space: nowrap;
  }
  .cta {
    position: absolute;
    background: var(--cta-bg);
    border-radius: 999px;
    color: var(--cta-red);
    font-family: "Open Sans", sans-serif;
    font-weight: 300;
    display: flex; align-items: center; justify-content: center;
    white-space: nowrap;
  }

  /* Skyscraper */
  .banner--tall { left: 146px; top: 349px; width: 240px; height: 480px; }
  .banner--tall .photo { left: 0; top: 0; width: 240px; height: 323px; }
  .banner--tall .title { left: 0; width: 240px; top: 284px; text-align: center; font-size: 32px; }
  .banner--tall .cta { left: 27px; top: 400px; width: 186px; height: 39px; font-size: 24px; }

  /* Leaderboard */
  .banner--wide { left: 472px; top: 399px; width: 582px; height: 72px; }
  .banner--wide .photo { left: 14px; top: 0; width: 144px; height: 72px; }
  .banner--wide .title { left: 175px; top: 20px; font-size: 22px; }
  .banner--wide .cta { left: 414px; top: 23px; width: 128px; height: 27px; font-size: 16px; }

  /* Medium rectangle */
  .banner--box { left: 613px; top: 516px; width: 299px; height: 250px; }
  .banner--box .photo { left: 13px; top: 0; width: 275px; height: 178px; }
  .banner--box .title { left: 0; width: 314px; top: 157px; text-align: center; font-size: 22px; }
  .banner--box .cta { left: 86px; top: 202px; width: 128px; height: 27px; font-size: 16px; }
</style>
</head>
<body>
  <section class="banner banner--tall">
    <div class="photo" role="img" aria-label="Photo of two studio microphones hanging against a dark background"></div>
    <h2 class="title">Brightwater<br>Hour</h2>
    <a class="cta">LEARN MORE</a>
  </section>

  <section class="banner banner--wide">
    <div class="photo" role="img" aria-label="Photo of two studio microphones hanging against a dark background"></div>
    <h2 class="title">Brightwater Hour</h2>
    <a class="cta">LEARN MORE</a>
  </section>

  <section class="banner banner--box">
    <div class="photo" role="img" aria-label="Photo of two studio microphones hanging against a dark background"></div>
    <h2 class="title">Brightwater Hour</h2>
    <a class="cta">LEARN MORE</a>
  </section>
</body>
</html>
```